INSTAGRAM STORY FEED FOR LUXURY JEWELRY STORE

For a luxury jewelry retailer. We want to create a set of posts for feed for the post-covid world once we reopen. Our goal is to emphasize the rebirth, the beggining of a new day, with focuses on the REAL important things in life: LOVE (through an engagement rings). LIFE (through baby birth gifts). HAPINESS (through benchmark moments like anniversaries).
Colors must be elegant but happy.
for refference our company Instagram is @quorvane_official so you can have a feel of our brand and product.

Target Market(s)

ENGAGEMENT RINGS. DIAMOND CUSTOMERS. LUXURY RETAIL. LATIN AMERICA.

Industry/Entity Type

Jewelry

Other font styles liked:
• Our logo uses AUDREY

Requirements
Must have
• THEME MUST BE BASED ON A NEW DAY. ELEGANT COLOR SCHEME, WITH LIGHT COLORS, MUST INCLUDE SEVERAL POSTS FOR INSTAGRAM FEED INCLUDING:
Our goal is to emphasize the rebirth, the beggining of a new day, with focuses on the REAL important things in life: LOVE (through an engagement rings). LIFE (through baby birth gifts). HAPINESS (through benchmark moments like anniversaries).
Nice to have
• CLEAN LOOK. PLEASE VIEW IMAGE EXAMPLES OF THINGS I LIKE.
I HAVE POSTED A “LOVE” SIGN IN IMAGES. It would be nice to make something like that sign, in black font, and white, light grey, or even yellow background, and have a ring or piece of jewelrry balancing or hanging from
One of the letters. Then do something similar with word Life, etc.
Should not have
• NO BLACK. NO DARK COLORS. NOTHING THAT WILL LOOK TACKY.

```html
<!DOCTYPE html>
<html lang="en">
<head>
<meta charset="UTF-8">
<title>Quorvane — Happines · A New Day</title>
<link rel="stylesheet" href="https://fonts.googleapis.com/css2?family=Tenor+Sans&display=swap">
<style>
  :root {
    --paper: #f1f1f3;
    --paper-light: #f8f8f9;
    --gold: #958a6c;
    --gold-line: #8d8163;
    --gem-blue: #bcd8ee;
    --gem-clear: #e4e8ec;
    --gem-teal: #b7e6df;
    --gem-pink: #efc6ea;
    --gem-deep: #9fcfd8;
  }
  * { margin: 0; padding: 0; box-sizing: border-box; }
  html, body {
    width: 675px;
    height: 1200px;
    overflow: hidden;
    background: var(--paper);
  }
  .story {
    position: relative;
    width: 675px;
    height: 1200px;
    overflow: hidden;
    background: linear-gradient(180deg, var(--paper-light) 0%, var(--paper) 100%);
    font-family: "Tenor Sans", sans-serif;
    color: var(--gold);
  }
  .gem-photo {
    position: absolute;
    left: 84px;
    top: 150px;
    width: 232px;
    height: 930px;
    border-radius: 116px;
    background: linear-gradient(180deg,
      var(--gem-blue) 0%,
      var(--gem-clear) 22%,
      var(--gem-teal) 45%,
      var(--gem-pink) 68%,
      var(--gem-deep) 90%,
      var(--paper) 100%);
    opacity: 0.75;
    filter: blur(6px);
  }
  .frame {
    position: absolute;
    left: 0;
    top: 0;
  }
  .brand {
    position: absolute;
    left: 0;
    width: 675px;
    top: 18px;
    display: flex;
    flex-direction: column;
    align-items: center;
  }
  .brand-mark {
    width: 16px;
    height: 16px;
    border: 1.5px solid var(--gold);
    margin-bottom: 14px;
  }
  .brand-name {
    font-size: 25px;
    letter-spacing: 0.32em;
    padding-left: 0.32em;
    line-height: 1;
  }
  .headline {
    position: absolute;
    left: 446px;
    top: 196px;
    width: 70px;
    display: flex;
    flex-direction: column;
    align-items: center;
    font-size: 104px;
    line-height: 102px;
  }
  .headline span { display: block; }
  .tagline {
    position: absolute;
    left: 0;
    width: 675px;
    top: 1083px;
    text-align: center;
    font-size: 26px;
    letter-spacing: 0.12em;
    padding-left: 0.12em;
    line-height: 1;
  }
</style>
</head>
<body>
  <main class="story">
    <div class="gem-photo" role="img" aria-label="Photograph of five faceted gemstones in a vertical row — light blue, clear, aqua green, pink and deep teal — casting soft coloured shadows on a white surface"></div>

    <svg class="frame" width="675" height="1200" viewBox="0 0 675 1200" aria-hidden="true">
      <path d="M216 53 H44 V1147 H631 V53 H481" fill="none" stroke="var(--gold-line)" stroke-width="1.2"/>
    </svg>

    <header class="brand">
      <div class="brand-mark"></div>
      <div class="brand-name">QUORVANE</div>
    </header>

    <h1 class="headline" aria-label="HAPPINES">
      <span>H</span><span>A</span><span>P</span><span>P</span><span>I</span><span>N</span><span>E</span><span>S</span>
    </h1>

    <p class="tagline"># A NEW DAY</p>
  </main>
</body>
</html>
```